Residential real estate home builder in west texas

We need a website design for our home building business based in west Texas called Birch Hollow homes. We build new construction for potential homeowners in Amarillo. Currently we do not have any completed construction, but we have floor plans and architectural drawings of the front elevation. The website would need to be able to properly advertise a architectural drawing, floor plans, and descriptive content at the initial phase. The website will need to be simple but professional with generic picture content.
The website will need the ability to be updated in the future for the additions of home pictures, and video content and virtual tours of the homes.

Target Market(s)

Potential Home buyers

Industry/Entity Type

Real Estate

Number of Pages Required

5+ page

Font styles to use
Sans Serif

Colors
f37122
757575

Requirements
Must have
• Web design must be simple and easy to navigate. There is not much picture content, so it will need to be simple.
• 5 pages:
• Home, Available homes, Available floor plans, guide to ownership, Contact
• The website will need the ability to be updated in the future for the additions of pictures, and video content of the homes when they are built. ( A virtual tour).
Nice to have
• I would like to see a modern and cohesive design. Contact information at the bottom of each page.
Should not have
• A Black background

```html
<!DOCTYPE html>
<html lang="en">
<head>
<meta charset="utf-8">
<title>Birch Hollow Homes</title>
<link href="https://fonts.googleapis.com/css2?family=Raleway:wght@500;600;700;800&family=Open+Sans:ital,wght@0,400;0,600;0,700;1,400&display=swap" rel="stylesheet">
<style>
:root{
  --orange:#f37122;
  --grey:#757575;
  --dark:#2f2f2f;
  --text:#555;
  --line:#dcdcdc;
  --white:#fff;
}
*{margin:0;padding:0;box-sizing:border-box}
html,body{width:1200px;height:3077px;overflow:hidden;background:var(--white)}
body{position:relative;font-family:"Open Sans",Arial,sans-serif;color:var(--text)}
.abs{position:absolute}
.section-title{position:absolute;left:0;width:1200px;text-align:center;font-family:"Raleway",Arial,sans-serif;font-weight:700;font-size:31px;color:var(--dark);letter-spacing:.5px}

/* header */
.header{position:absolute;left:0;top:0;width:1200px;height:103px;background:var(--white)}
.topbar{position:absolute;left:585px;top:0;width:530px;height:34px}
.topbar span{position:absolute;top:6px;color:var(--white);font-size:17px;font-weight:600}
.brand{position:absolute;left:96px;top:30px;display:flex;align-items:center;gap:10px;font-family:"Raleway",Arial,sans-serif;font-weight:700;font-size:27px;color:var(--grey);letter-spacing:.5px}
.brand i{display:block;width:18px;height:18px;background:var(--orange)}
.nav{position:absolute;top:58px;font-size:16px;color:var(--dark)}
.nav.active{color:var(--orange)}

/* hero */
.hero{position:absolute;left:0;top:103px;width:1200px;height:465px;background:linear-gradient(135deg,#5a4634 0%,#8a7058 35%,#6b5743 60%,#3e3027 100%)}
.hero-title{position:absolute;top:230px;width:1200px;text-align:center;font-family:"Raleway",Arial,sans-serif;font-weight:800;font-size:48px;color:var(--white);letter-spacing:1px}
.hero-sub{position:absolute;top:304px;width:1200px;text-align:center;font-size:20px;font-weight:600;color:var(--white)}
.hero-btn{position:absolute;left:507px;top:357px;width:186px;height:47px;border:2px solid var(--white);color:var(--white);font-size:16px;font-weight:700;text-align:center;line-height:43px}
.dots{position:absolute;top:503px;left:563px;display:flex;gap:6px}
.dots i{display:block;width:13px;height:13px;border:2px solid var(--white);border-radius:50%}
.dots i.on{background:var(--white)}

/* welcome */
.intro{position:absolute;top:690px;left:250px;width:700px;text-align:center;font-size:13.5px;line-height:28px;color:#777}
.feature{position:absolute;top:767px;width:240px;text-align:center}
.feature .ring{width:164px;height:164px;margin:0 auto;border:2px solid #777;border-radius:50%;display:flex;align-items:center;justify-content:center}
.feature h3{margin-top:30px;font-family:"Raleway",Arial,sans-serif;font-weight:700;font-size:19px;color:var(--dark)}
.feature p{margin-top:12px;font-size:12.5px;line-height:24px;color:#888}

/* video */
.video-band{position:absolute;left:0;top:1124px;width:1200px;height:550px;background:linear-gradient(90deg,#ececec,#fafafa 30%,#fff 50%,#fafafa 70%,#e8e8e8)}
.video{position:absolute;left:277px;top:1253px;width:646px;height:361px;border:5px solid #f2f2f2;box-shadow:0 0 6px rgba(0,0,0,.25);background:linear-gradient(180deg,#c9c2b8 0%,#e6e1da 40%,#8d8278 75%,#5b5048 100%)}
.play{position:absolute;left:298px;top:155px;width:50px;height:50px;border-radius:50%;background:rgba(0,0,0,.55)}

/* blog */
.post{position:absolute;top:1836px;width:324px}
.post .thumb{width:324px;height:215px;border:2px solid #e4e4e4}
.post .date{position:absolute;left:-6px;top:139px;width:46px;height:62px;background:var(--orange);color:var(--white);text-align:center}
.post .date b{display:block;font-size:24px;line-height:32px}
.post .date small{display:block;font-size:12px}
.post h3{margin-top:30px;font-family:"Raleway",Arial,sans-serif;font-weight:700;font-size:19px;color:var(--dark)}
.post p{margin-top:12px;font-size:12.5px;line-height:23px;color:#777;padding-bottom:14px;border-bottom:1px solid var(--line)}
.post .meta{margin-top:14px;font-size:12.5px;color:#777;display:flex;gap:24px}
.post .meta span{color:var(--orange);margin-right:4px}

/* testimonials */
.testimonials{position:absolute;left:0;top:2297px;width:1200px;height:361px;background:var(--orange)}
.testimonials .section-title{color:var(--white);top:0;position:relative;padding-top:64px}
.quote{position:absolute;top:120px;width:320px}
.quote .avatar{position:absolute;left:0;top:30px;width:76px;height:76px;border-radius:50%;border:3px solid #fff;background:linear-gradient(#e6c9b2,#c8a184)}
.quote p{position:absolute;left:90px;top:26px;width:230px;font-style:italic;font-size:12.5px;line-height:24px;color:var(--white)}
.quote p b{font-size:22px;font-style:normal;margin-right:6px}
.quote h4{position:absolute;left:90px;top:116px;font-size:10.5px;font-weight:700;color:var(--white)}
.quote small{position:absolute;left:90px;top:134px;font-size:9.5px;font-style:italic;color:var(--white);white-space:nowrap}
.quote .stars{position:absolute;left:90px;top:164px;font-size:20px;color:#ffd21f;letter-spacing:3px}
.arrow{position:absolute;top:192px;width:36px;height:36px;border:2px solid var(--white);border-radius:50%}

/* footer */
.footer-brand{position:absolute;left:92px;top:2810px;display:flex;align-items:center;gap:10px;font-family:"Raleway",Arial,sans-serif;font-weight:700;font-size:27px;color:var(--grey)}
.footer-brand i{display:block;width:18px;height:18px;background:var(--orange)}
.fcol{position:absolute;top:2737px}
.fcol h4{font-family:"Raleway",Arial,sans-serif;font-weight:700;font-size:19px;color:var(--dark);margin-bottom:26px}
.fcol li{list-style:none;font-size:12.5px;color:#666;line-height:33.5px}
.fcol p{font-size:12.5px;color:#666;line-height:24px;width:270px}
.email-field{margin-top:16px;width:255px;border-bottom:1px solid #bbb;font-size:11.5px;color:#aaa;padding:8px 12px}
.btn-sub{margin-top:16px;width:104px;height:34px;background:var(--orange);color:var(--white);font-size:11px;font-weight:700;text-align:center;line-height:34px;border-radius:3px}
.contact-row{display:flex;gap:18px;font-size:12.5px;color:#666;line-height:20px;margin-bottom:12px}
.contact-row svg{flex:none;margin-top:2px}
.rule{position:absolute;left:98px;top:2999px;width:1004px;height:1px;background:var(--line)}
.copy{position:absolute;left:98px;top:3026px;font-size:12px;color:#555}
.social{position:absolute;top:3022px;width:24px;height:24px;border:1.5px solid var(--orange);border-radius:50%}
</style>
</head>
<body>

<header class="header">
  <svg class="topbar" viewBox="0 0 530 34" aria-hidden="true">
    <polygon points="0,0 196,0 180,34 16,34" fill="var(--orange)"/>
    <polygon points="210,0 530,0 512,34 226,34" fill="var(--orange)"/>
  </svg>
  <span class="abs" style="left:612px;top:6px;color:#fff;font-size:17px;font-weight:600">&#9742; 1 555 010 0100</span>
  <span class="abs" style="left:828px;top:6px;color:#fff;font-size:17px;font-weight:600">&#9993; info@birchhollowhomes.com</span>
  <div class="brand"><i></i>Birch Hollow Homes</div>
  <span class="nav active" style="left:422px">Home</span>
  <span class="nav" style="left:492px">Available homes</span>
  <span class="nav" style="left:646px">Available floor plans</span>
  <span class="nav" style="left:826px">Guide to ownership</span>
  <span class="nav" style="left:1001px">Contact</span>
  <svg class="abs" style="left:1084px;top:60px" width="18" height="18" viewBox="0 0 18 18" aria-hidden="true"><circle cx="7" cy="7" r="5" fill="none" stroke="#2f2f2f" stroke-width="2.2"/><line x1="11" y1="11" x2="16" y2="16" stroke="#2f2f2f" stroke-width="2.6"/></svg>
</header>

<section class="hero" role="img" aria-label="Builders working on a house frame with scaffolding">
  <h1 class="hero-title" style="top:127px">BIRCH HOLLOW HOMES</h1>
  <p class="hero-sub" style="top:201px">We build new construction for potential homeowners in Amarillo</p>
  <div class="hero-btn" style="top:254px">GET MORE INFO</div>
  <div class="dots" style="top:400px"><i class="on"></i><i></i><i></i><i></i></div>
</section>

<h2 class="section-title" style="top:628px">WELCOME TO BIRCH HOLLOW HOMES</h2>
<p class="intro">Nam libero tempore, cum soluta nobis est eligendi optio cumque nihil impedit quo minus id quod maxime placeat facere possimus, omnis voluptas assumenda est, omnis dolor repellend poribus autem quibusdam</p>

<div class="feature" style="left:85px">
  <div class="ring"><svg width="56" height="56" viewBox="0 0 56 56" aria-hidden="true"><rect x="6" y="24" width="10" height="24" fill="var(--orange)"/><path d="M19 24 L30 8 Q35 6 35 12 L33 22 H47 Q51 23 50 28 L46 46 Q45 48 42 48 H19 Z" fill="var(--orange)"/></svg></div>
  <h3>High Quality</h3>
  <p>At vero eos et accusamus et iusto odio dignissimos ducimus qui blandit</p>
</div>
<div class="feature" style="left:348px">
  <div class="ring"><svg width="56" height="56" viewBox="0 0 56 56" aria-hidden="true"><rect x="13" y="5" width="30" height="46" fill="none" stroke="var(--orange)" stroke-width="3"/><g fill="var(--orange)"><rect x="18" y="11" width="5" height="5"/><rect x="25.5" y="11" width="5" height="5"/><rect x="33" y="11" width="5" height="5"/><rect x="18" y="20" width="5" height="5"/><rect x="25.5" y="20" width="5" height="5"/><rect x="33" y="20" width="5" height="5"/><rect x="18" y="29" width="5" height="5"/><rect x="25.5" y="29" width="5" height="5"/><rect x="33" y="29" width="5" height="5"/><rect x="24" y="39" width="8" height="12"/></g></svg></div>
  <h3>Professionalism</h3>
  <p>At vero eos et accusamus et iusto odio dignissimos ducimus qui blandit</p>
</div>
<div class="feature" style="left:610px">
  <div class="ring"><svg width="56" height="56" viewBox="0 0 56 56" aria-hidden="true"><polygon fill="var(--orange)" points="28,4 33,12 42,9 42,18 51,22 45,29 51,36 42,39 42,48 33,45 28,53 23,45 14,48 14,39 5,36 11,29 5,22 14,18 14,9 23,12"/></svg></div>
  <h3>Experienced</h3>
  <p>At vero eos et accusamus et iusto odio dignissimos ducimus qui blandit</p>
</div>
<div class="feature" style="left:873px">
  <div class="ring"><svg width="64" height="56" viewBox="0 0 64 56" aria-hidden="true"><g fill="var(--orange)"><circle cx="14" cy="16" r="7"/><circle cx="50" cy="16" r="7"/><circle cx="32" cy="14" r="9"/><path d="M2 44 Q2 26 14 26 Q22 26 24 32 V44 Z"/><path d="M62 44 Q62 26 50 26 Q42 26 40 32 V44 Z"/><path d="M18 50 Q18 26 32 26 Q46 26 46 50 Z"/></g></svg></div>
  <h3>Customization</h3>
  <p>At vero eos et accusamus et iusto odio dignissimos ducimus qui blandit</p>
</div>

<section class="video-band" role="img" aria-label="Light pencil sketch of city buildings as background"></section>
<h2 class="section-title" style="top:1180px">WATCH OUR VIDEO</h2>
<div class="video" role="img" aria-label="Video preview of a furnished kitchen and dining room">
  <div class="play"><svg width="50" height="50" viewBox="0 0 50 50" aria-hidden="true"><polygon points="19,14 37,25 19,36" fill="#fff"/></svg></div>
</div>

<h2 class="section-title" style="top:1756px">LATEST BLOG</h2>
<article class="post" style="left:94px">
  <div class="thumb" role="img" aria-label="Hands reviewing rolled architectural plans" style="background:linear-gradient(135deg,#e7d6bf,#c9a47c 55%,#8b6a4c)"></div>
  <div class="date"><b>01</b><small>NOV</small></div>
  <h3>Finibus Bonorum et Malorum</h3>
  <p>Nam libero tempore, cum soluta nobis est eligendi optio cumque nihil impedit quo minus id quod maxim.</p>
  <div class="meta"><div><span>&#9679;</span>John Doe</div><div><span>&#9632;</span>3 Comments</div></div>
</article>
<article class="post" style="left:439px">
  <div class="thumb" role="img" aria-label="Architect on the phone beside a building model" style="background:linear-gradient(135deg,#9aa7ad,#d8dcdc 50%,#6f7a80)"></div>
  <div class="date"><b>01</b><small>NOV</small></div>
  <h3>Finibus Bonorum et Malorum</h3>
  <p>Nam libero tempore, cum soluta nobis est eligendi optio cumque nihil impedit quo minus id quod maxim.</p>
  <div class="meta"><div><span>&#9679;</span>John Doe</div><div><span>&#9632;</span>3 Comments</div></div>
</article>
<article class="post" style="left:783px">
  <div class="thumb" role="img" aria-label="Wireframe rendering of a building structure" style="background:linear-gradient(135deg,#f2f2f4,#b8bde0 50%,#d9d9de)"></div>
  <div class="date"><b>01</b><small>NOV</small></div>
  <h3>Finibus Bonorum et Malorum</h3>
  <p>Nam libero tempore, cum soluta nobis est eligendi optio cumque nihil impedit quo minus id quod maxim.</p>
  <div class="meta"><div><span>&#9679;</span>John Doe</div><div><span>&#9632;</span>3 Comments</div></div>
</article>

<section class="testimonials">
  <h2 class="section-title">CLIENT TESTIMONIALS</h2>
  <svg class="arrow" style="left:27px" viewBox="0 0 36 36" aria-hidden="true"><polyline points="20,11 13,18 20,25" fill="none" stroke="#fff" stroke-width="2.5"/></svg>
  <svg class="arrow" style="left:1135px" viewBox="0 0 36 36" aria-hidden="true"><polyline points="15,11 22,18 15,25" fill="none" stroke="#fff" stroke-width="2.5"/></svg>
  <div class="quote" style="left:97px">
    <div class="avatar" role="img" aria-label="Client portrait"></div>
    <p><b>&ldquo;</b>At vero eos et accusamus et iustodio dignissimos ducimus qui blanditiipraesent ium voluptatum deleniti atq.</p>
    <h4>MARLA FENWICK</h4><small>Financial Services Professional</small>
    <div class="stars">&#9733;&#9733;&#9733;&#9733;&#9734;</div>
  </div>
  <div class="quote" style="left:448px">
    <div class="avatar" role="img" aria-label="Client portrait" style="background:linear-gradient(#d7d7d7,#9a9a9a)"></div>
    <p><b>&ldquo;</b>At vero eos et accusamus et iustodio dignissimos ducimus qui blanditiipraesent ium voluptatum deleniti atq.</p>
    <h4>DORIAN P. HOLT</h4><small>Urban Planning Fellow</small>
    <div class="stars">&#9733;&#9733;&#9733;&#9733;&#9734;</div>
  </div>
  <div class="quote" style="left:794px">
    <div class="avatar" role="img" aria-label="Client portrait" style="background:linear-gradient(#eadccd,#c5a78c)"></div>
    <p><b>&ldquo;</b>At vero eos et accusamus et iustodio dignissimos ducimus qui blanditiipraesent ium voluptatum deleniti atq.</p>
    <h4>RUTH CALLOWAY</h4><small>Creative Strategist | Entrepreneur</small>
    <div class="stars">&#9733;&#9733;&#9733;&#9733;&#9734;</div>
  </div>
</section>

<footer>
  <div class="footer-brand"><i></i>Birch Hollow Homes</div>
  <div class="fcol" style="left:400px">
    <h4>Quick Links</h4>
    <ul><li>Home</li><li>Available homes</li><li>Available floor plans</li><li>Guide to ownership</li><li>Contact</li></ul>
  </div>
  <div class="fcol" style="left:593px">
    <h4>Newsletter Subscription</h4>
    <p>Register your Email Address to get information about us</p>
    <div class="email-field">Email Address</div>
    <div class="btn-sub">SUBSCRIBE</div>
  </div>
  <div class="fcol" style="left:913px">
    <h4>Contact Us</h4>
    <div class="contact-row"><svg width="12" height="16" viewBox="0 0 12 16"><path d="M6 0 A6 6 0 0 1 12 6 C12 10 6 16 6 16 C6 16 0 10 0 6 A6 6 0 0 1 6 0Z" fill="var(--orange)"/><circle cx="6" cy="6" r="2.2" fill="#fff"/></svg><span>Suite 12, 400 Canyon Road<br>Amarillo TX 79101</span></div>
    <div class="contact-row"><svg width="14" height="14" viewBox="0 0 14 14"><path d="M2 1 L5 1 L6 4 L4 6 Q6 9 8 10 L10 8 L13 9 L13 12 Q7 13 3 8 Q0 4 2 1Z" fill="var(--orange)"/></svg><span>1 555 010 0100</span></div>
    <div class="contact-row"><svg width="14" height="14" viewBox="0 0 14 14"><rect x="1" y="4" width="12" height="9" fill="var(--orange)"/><rect x="3" y="1" width="8" height="4" fill="var(--orange)"/><rect x="3" y="7" width="8" height="2" fill="#fff"/></svg><span>1 555 010 0199</span></div>
    <div class="contact-row"><svg width="14" height="12" viewBox="0 0 14 12"><rect x="0" y="1" width="14" height="10" fill="var(--orange)"/><polyline points="0,1 7,7 14,1" fill="none" stroke="#fff" stroke-width="1.3"/></svg><span>info@birchhollowhomes.com</span></div>
  </div>
  <div class="rule"></div>
  <p class="copy">Copyrights &copy; 2017,&nbsp; Birch Hollow homes. All rights reserved.</p>
  <span class="social" style="left:977px"></span>
  <span class="social" style="left:1010px"></span>
  <span class="social" style="left:1043px"></span>
  <span class="social" style="left:1076px"></span>
</footer>

</body>
</html>
```